K&T Powerline Depot Business Cards

This will be used a business cards. Would love an industrial type flavor paired with the floating/3d is design like attached.

Do not have any certain colors picked out but something that will look good and stand out!!!.

K&T Powerline Depot
"Keeping your lights on"

The business does home standby Generators..

Contact Information for Business Card

K&T Powerline Depot

Requirements
Must have
• Would love an industrial type flavor paired with the floating/3d is design like attached for a sample.

```html
<!DOCTYPE html>
<html lang="en">
<head>
<meta charset="UTF-8">
<title>K&amp;T Powerline Depot – Business Cards</title>
<link href="https://fonts.googleapis.com/css2?family=Montserrat:wght@500;600;700;800&family=Ubuntu:ital,wght@1,500&family=Arimo:wght@400&display=swap" rel="stylesheet">
<style>
  :root {
    --stage: #2b2b2b;
    --stage-edge: #1c1c1c;
    --card: #0d0d0d;
    --card-soft: #161616;
    --brand-blue: #0b5b9c;
    --brand-green: #7cc41f;
    --silver: #d9d9d9;
    --ink-light: #f4f4f4;
    --divider: #2c2c2c;
  }
  * { margin: 0; padding: 0; box-sizing: border-box; }
  html, body { width: 1200px; height: 900px; overflow: hidden; }
  body {
    background: radial-gradient(ellipse at 50% 35%, var(--stage) 0%, var(--stage-edge) 100%);
    font-family: "Montserrat", sans-serif;
    position: relative;
  }
  .card {
    position: absolute;
    width: 560px;
    height: 320px;
    border-radius: 22px;
    background: linear-gradient(160deg, var(--card-soft) 0%, var(--card) 60%);
    box-shadow: 0 18px 40px rgba(0,0,0,0.55);
  }
  .card--back { left: 580px; top: 90px; }
  .card--front { left: 80px; top: 470px; }

  /* Back */
  .back-brand {
    position: absolute; inset: 0;
    display: flex; flex-direction: column; align-items: center; justify-content: center;
    gap: 12px;
  }
  .back-brand .brand-name {
    font-weight: 800; font-size: 34px; letter-spacing: 0.5px;
    color: var(--silver);
  }
  .back-brand .tagline { color: var(--silver); font-size: 22px; }

  /* Front */
  .front-brand {
    position: absolute; left: 0; top: 0; width: 262px; height: 100%;
    display: flex; flex-direction: column; justify-content: center;
    padding-left: 30px; padding-top: 60px; gap: 8px;
  }
  .front-brand .brand-mark {
    width: 24px; height: 24px; background: var(--brand-green);
  }
  .front-brand .brand-name {
    font-weight: 800; font-size: 19px; line-height: 1.1; white-space: nowrap;
    color: var(--brand-blue);
  }
  .front-brand .tagline { color: var(--brand-green); font-size: 16px; }
  .tagline { font-family: "Ubuntu", sans-serif; font-style: italic; font-weight: 500; }

  .divider {
    position: absolute; left: 262px; top: 40px; bottom: 40px;
    width: 1px; background: var(--divider);
  }
  .contact {
    position: absolute; left: 290px; top: 44px; right: 20px;
    color: var(--ink-light);
  }
  .contact .person {
    font-weight: 600; font-size: 21px; letter-spacing: -0.3px; text-transform: uppercase;
  }
  .person .first { color: var(--brand-blue); }
  .person .last { color: var(--brand-green); }
  .contact .role { font-family: "Arimo", sans-serif; font-size: 15px; margin-top: 2px; }
  .contact-list { list-style: none; margin-top: 16px; }
  .contact-list li {
    display: flex; align-items: center; gap: 8px;
    font-family: "Arimo", sans-serif; font-size: 14.5px; line-height: 23px;
  }
  .contact-list svg { width: 17px; height: 17px; flex: none; }
  .address {
    font-family: "Arimo", sans-serif; font-size: 14.5px; line-height: 20px;
    margin-top: 18px; margin-left: 25px;
  }
</style>
</head>
<body>

<section class="card card--back" aria-label="Card back">
  <div class="back-brand">
    <div class="brand-name">K&amp;T Powerline Depot</div>
    <div class="tagline">Keeping your lights on</div>
  </div>
</section>

<section class="card card--front" aria-label="Card front">
  <div class="front-brand">
    <div class="brand-mark"></div>
    <div class="brand-name">K&amp;T Powerline Depot</div>
    <div class="tagline">Keeping your lights on</div>
  </div>
  <div class="divider"></div>
  <div class="contact">
    <div class="person"><span class="first">Marcus</span> <span class="last">Hale</span></div>
    <div class="role">Managing Director</div>
    <ul class="contact-list">
      <li>
        <svg viewBox="0 0 20 20" aria-hidden="true"><circle cx="10" cy="10" r="10" fill="var(--brand-green)"/><path d="M6.5 5.5c.6-.6 1.4-.3 1.7.3l.8 1.6c.2.5 0 .9-.3 1.2l-.6.5c.6 1.3 1.5 2.2 2.8 2.8l.5-.6c.3-.3.7-.5 1.2-.3l1.6.8c.6.3.9 1.1.3 1.7l-.8.8c-3.5.4-7.2-3.3-6.8-6.8z" fill="#0d0d0d"/></svg>
        055-210 734 618
      </li>
      <li>
        <svg viewBox="0 0 20 20" aria-hidden="true"><circle cx="10" cy="10" r="10" fill="var(--brand-green)"/><rect x="5" y="6.5" width="10" height="7" fill="#0d0d0d"/><path d="M5 6.5l5 4 5-4" stroke="var(--brand-green)" stroke-width="1" fill="none"/></svg>
        hello@ktpowerline.com
      </li>
      <li>
        <svg viewBox="0 0 20 20" aria-hidden="true"><circle cx="10" cy="10" r="10" fill="var(--brand-green)"/><circle cx="10" cy="10" r="5" fill="none" stroke="#0d0d0d" stroke-width="1.3"/><path d="M5 10h10M10 5c-2.5 3-2.5 7 0 10M10 5c2.5 3 2.5 7 0 10" stroke="#0d0d0d" stroke-width="1" fill="none"/></svg>
        www.ktpowerline.com
      </li>
    </ul>
    <div class="address">188, Foundry Road North<br>30917, Riverton</div>
  </div>
</section>

</body>
</html>
```